Brookvale Building Company - advertisement poster

I am looking to print some canvas signs to advertise my general contracting company, Brookvale Building Company. The sign will measure 6' long x 3' high so the size should match that ratio. I already have a logo icon, which is the Letter 'B' and some trees that I would like to incorporate, see attached. I would also like the to have the following information listed:
1) phone number: 831-555-0172
2) email: brookvalebuildingcompany@mailnest.example
3) website: brookvalebuildingcompany.example
4) Lic#4826130
5) I want to use this text: "BUILD WITH THE B-CREW!"

The ad should be relatively simple and clean. Black and Green are my company colors. I am open to creative ideas!

Target Market(s)

People looking to renovate their homes

Industry/Entity Type

Construction

Colors
59FF00
82FF00
B8FF75
E3FFCB
F4FFEA

Requirements
Must have
• Must have my company logo
Should not have
• No photos or complex graphics

```html
<!DOCTYPE html>
<html lang="en">
<head>
<meta charset="utf-8">
<title>Brookvale Building Company – Sign</title>
<link href="https://fonts.googleapis.com/css2?family=Orbitron:wght@500;800&family=Quicksand:wght@500&display=swap" rel="stylesheet">
<style>
  :root {
    --page: #ffffff;
    --green: #72b346;
    --green-mid: #5e8b3e;
    --green-deep: #44632f;
    --charcoal: #191919;
    --black: #000000;
    --white: #ffffff;
  }
  html, body {
    margin: 0;
    width: 1200px;
    height: 963px;
    overflow: hidden;
    background: var(--page);
  }
  .sign {
    position: absolute;
    left: 158px;
    top: 263px;
    width: 897px;
    height: 448px;
    overflow: hidden;
  }
  .sign-backdrop {
    position: absolute;
    inset: 0;
    width: 897px;
    height: 448px;
  }
  .headline {
    position: absolute;
    left: 58px;
    top: 128px;
    margin: 0;
    font-family: "Orbitron", sans-serif;
    font-weight: 800;
    font-size: 52px;
    line-height: 68px;
    letter-spacing: 2px;
    color: var(--white);
  }
  .contact-list {
    position: absolute;
    left: 56px;
    top: 392px;
    margin: 0;
    padding: 0;
    list-style: none;
    font-family: "Quicksand", sans-serif;
    font-weight: 500;
    font-size: 12.5px;
    letter-spacing: 0.6px;
    color: var(--green);
  }
  .contact-list li {
    display: flex;
    align-items: center;
    gap: 9px;
    height: 21px;
  }
  .contact-icon { width: 13px; height: 13px; flex: none; }
  .phone {
    position: absolute;
    left: 632px;
    top: 38px;
    display: flex;
    align-items: center;
    gap: 10px;
    font-family: "Orbitron", sans-serif;
    font-weight: 500;
    font-size: 21px;
    letter-spacing: 2px;
    color: var(--green);
  }
  .phone-icon { width: 20px; height: 20px; }
  .brand-mark {
    position: absolute;
    left: 634px;
    top: 200px;
    width: 60px;
    height: 60px;
    background: var(--green);
  }
  .brand-name {
    position: absolute;
    left: 440px;
    width: 448px;
    top: 296px;
    margin: 0;
    text-align: center;
    font-family: "Orbitron", sans-serif;
    font-weight: 800;
    color: var(--white);
  }
  .brand-name .line-main {
    display: block;
    font-size: 43px;
    line-height: 48px;
    letter-spacing: 1px;
  }
  .brand-name .line-sub {
    display: block;
    font-size: 17.5px;
    line-height: 22px;
    letter-spacing: 6px;
  }
  .license {
    position: absolute;
    left: 440px;
    width: 448px;
    top: 394px;
    text-align: center;
    font-family: "Orbitron", sans-serif;
    font-weight: 500;
    font-size: 15px;
    letter-spacing: 2px;
    color: var(--green);
  }
</style>
</head>
<body>
  <section class="sign">
    <svg class="sign-backdrop" viewBox="0 0 897 448" aria-hidden="true">
      <rect width="897" height="448" fill="var(--black)"/>
      <polygon points="0,0 537,0 405,186 474,186 366,333 441,333 356,448 0,448" fill="var(--charcoal)"/>
      <polygon points="0,0 304,0 0,436" fill="var(--green-deep)"/>
      <polygon points="0,0 268,0 0,386" fill="var(--green-mid)"/>
      <polygon points="0,0 233,0 0,334" fill="var(--green)"/>
      <polyline points="537,0 405,186 474,186 366,333 441,333 356,448" fill="none" stroke="var(--green)" stroke-width="3"/>
    </svg>

    <h1 class="headline">BUILD<br>WITH THE<br>B-CREW!</h1>

    <ul class="contact-list">
      <li>
        <svg class="contact-icon" viewBox="0 0 14 14" fill="none" stroke="currentColor" stroke-width="1.3"><rect x="1" y="2.5" width="12" height="9" rx="1.5"/><polyline points="1.5,3.5 7,8 12.5,3.5"/></svg>
        brookvalebuildingcompany@mailnest.example
      </li>
      <li>
        <svg class="contact-icon" viewBox="0 0 14 14" fill="none" stroke="currentColor" stroke-width="1.2"><circle cx="7" cy="7" r="6"/><ellipse cx="7" cy="7" rx="2.6" ry="6"/><line x1="1" y1="7" x2="13" y2="7"/><line x1="2" y1="4" x2="12" y2="4"/><line x1="2" y1="10" x2="12" y2="10"/></svg>
        brookvalebuildingcompany.example
      </li>
    </ul>

    <div class="phone">
      <svg class="phone-icon" viewBox="0 0 24 24" fill="none" stroke="currentColor" stroke-width="1.6" stroke-linejoin="round"><path d="M5 3h3.5l1.8 4.5-2.3 1.5a11 11 0 0 0 7 7l1.5-2.3L21 15.5V19a2 2 0 0 1-2 2A16 16 0 0 1 3 5a2 2 0 0 1 2-2z"/></svg>
      831-555-0172
    </div>

    <div class="brand-mark" aria-hidden="true"></div>
    <h2 class="brand-name">
      <span class="line-main">BROOKVALE</span>
      <span class="line-sub">BUILDING COMPANY</span>
    </h2>

    <div class="license">LIC# 4826130</div>
  </section>
</body>
</html>
```